Veldmark Supplies Business Card

Professional business card that stand out to our potential customers. Front and back with clean modern design

Industry/Entity Type

Oil and gas

Contact Information for Business Card

Name, address, website , office phone and cell number

Requirements
Must have
• Editable files for each employee

```html
<!DOCTYPE html>
<html lang="en">
<head>
<meta charset="utf-8">
<title>Veldmark Supplies Business Card</title>
<link href="https://fonts.googleapis.com/css2?family=Poppins:wght@400;700&display=swap" rel="stylesheet">
<style>
  :root {
    --page: #2b2b2d;
    --card: #262626;
    --red: #e62127;
    --blue: #1bafd0;
    --white: #ffffff;
    --rule: #8a8a8a;
  }
  * { margin: 0; padding: 0; box-sizing: border-box; }
  html, body { width: 1200px; height: 900px; overflow: hidden; }
  body {
    background: var(--page);
    font-family: "Poppins", sans-serif;
    position: relative;
  }
  .card {
    position: absolute;
    left: 260px;
    width: 680px;
    height: 390px;
    background: var(--card);
    border-radius: 22px;
    overflow: hidden;
    box-shadow: 0 8px 24px rgba(0,0,0,0.45);
  }
  .card-front { top: 40px; }
  .card-back { top: 470px; }

  .brand {
    display: flex;
    align-items: center;
    gap: 14px;
    color: var(--red);
    font-weight: 700;
    text-transform: uppercase;
    letter-spacing: 1px;
    white-space: nowrap;
  }
  .brand-mark { background: var(--blue); flex: none; }

  .card-front .brand {
    position: absolute;
    left: 50%; top: 50%;
    transform: translate(-50%, -50%);
    font-size: 40px;
  }
  .card-front .brand-mark { width: 34px; height: 34px; }

  .card-back .brand {
    position: absolute;
    left: 40px; top: 160px;
    font-size: 22px;
  }
  .card-back .brand-mark { width: 20px; height: 20px; }

  .divider {
    position: absolute;
    left: 345px; top: 70px;
    width: 1px; height: 200px;
    background: var(--rule);
  }
  .contact {
    position: absolute;
    left: 375px; top: 72px;
    color: var(--white);
  }
  .contact-name { color: var(--red); font-size: 26px; font-weight: 700; line-height: 1.1; }
  .contact-role { font-size: 15px; margin-bottom: 8px; }
  .contact-address { font-size: 15px; line-height: 1.35; margin-bottom: 4px; }
  .contact-list { list-style: none; font-size: 15px; line-height: 1.45; }
  .contact-list li { display: flex; align-items: center; gap: 10px; }
  .contact-list svg { width: 12px; height: 12px; fill: var(--red); flex: none; }

  .stripe {
    position: absolute;
    left: 0; bottom: 0;
    width: 100%; height: 16px;
  }
</style>
</head>
<body>

<section class="card card-front">
  <div class="brand"><span class="brand-mark"></span>Veldmark Supplies</div>
</section>

<section class="card card-back">
  <div class="brand"><span class="brand-mark"></span>Veldmark Supplies</div>
  <div class="divider"></div>
  <div class="contact">
    <p class="contact-name">Marcus Holt</p>
    <p class="contact-role">President</p>
    <p class="contact-address">415 N.Ridgeline Suite 7<br>Midland, Tx 79701</p>
    <ul class="contact-list">
      <li><svg viewBox="0 0 12 12"><path d="M2 1h3l1 3-1.5 1a7 7 0 0 0 2.5 2.5L8 6l3 1v3a1 1 0 0 1-1 1A9 9 0 0 1 1 2a1 1 0 0 1 1-1z"/></svg>(432)555-0187</li>
      <li><svg viewBox="0 0 12 12"><path d="M3 0h6a1 1 0 0 1 1 1v10a1 1 0 0 1-1 1H3a1 1 0 0 1-1-1V1a1 1 0 0 1 1-1zm0 2v7h6V2z"/></svg>(432)555-0193</li>
      <li><svg viewBox="0 0 12 12"><path d="M0 2h12v8H0zM1 3l5 4 5-4z"/></svg>sales@veldmarksupplies.com</li>
      <li><svg viewBox="0 0 12 12"><circle cx="6" cy="6" r="5.5"/></svg>www.veldmarksupplies.com</li>
    </ul>
  </div>
  <svg class="stripe" viewBox="0 0 680 16" preserveAspectRatio="none">
    <polygon points="0,0 345,0 330,16 0,16" fill="var(--red)"/>
    <polygon points="350,0 680,0 680,16 335,16" fill="var(--blue)"/>
  </svg>
</section>

</body>
</html>
```